Very basic draft completed. Need someone to apply their creative magic

I am building a new website for my business and looking for a designer to assist me on a part-time basis.

My business is a booking site for classes and lessons. It is essentially a directory service, and needs to conform to a standard web-layout that is easy to navigate and familiar to users (i.e. nothing to creative). The function and structure i have adopted is common amongst sites like zulk, hotel booking services, etc.

The first task on my list is to develop the main page. I have already compiled a draft of the first page using Fireworks (see attached) and am looking for someone to cast their creative magic to this draft while maintaining the general layout of the page. After the main page is developed, I will be looking for the same designer to assist with the rest of the site.

Design wise, I'd like to go for a slightly retro feel
By this I mean a moderately modern page with a spark of retro here and there. If you look at my draft you'll notice that I've used regular font for most text, and retro/old-school fonts for surburb names.

I happy for you to suggest colours, but regular page elements such as web links need to remain standard (i.e links = blue) so that they are familiar and identifiable to my users.

Other points:
1) I don't want the page to be too dark (dark headings, images and borders are fine, but I'd like to maintain white or light backgrounds)

2) Positioning: The Body should be centred, with the Header and Footer extending across the hole screen (as illustrated in my draft)

3) I'm happy if the design includes images from photostock libraries.The Silhoute picture for my draft were choosen because there are hundreds of them, and I can regularly change them on the site - keeping it fresh and new. I'd be very happy if the design incorporate images that could also be place often using photo stock images (i.e. happy to keep silhoutes, but leave it to you to decide what looks best)

Note: I'm happy for you to "copy" art work from any photo stock site, and I will pay for the full quality images when the design is selected.

4) The page Footer needs a lot of attention. It will contain standard Footer links/elements.

5) You are free to do anything to the Header section. It needs to have login/register elements

I'm happy to provide further comments, or review other sites/work to help direct design work.

Hi All,

I've updated the project brief, eliminating many of the requirements and giving you the freedom with design submissions, etc. I've also added the $20 payment for submissions. 
Cheers,
Corbin

Reason: I'm away on holiday and will review your submissions and provide feedback when I get back.

```html
<!DOCTYPE html>
<html lang="en">
<head>
<meta charset="utf-8">
<title>Out &amp; About – Courses &amp; Activities</title>
<link rel="stylesheet" href="https://fonts.googleapis.com/css2?family=Open+Sans:wght@400;600;700&display=swap">
<style>
:root{
  --ink:#1a1a1a;
  --black:#000;
  --bar:#0a0a0a;
  --panel:#f4f4f4;
  --card:#f1f1f1;
  --card-line:#dcdcdc;
  --muted:#8a8a8a;
  --accent:#e3134d;
  --login-bg:#3b3b3b;
  --field:#d9d9d9;
  --white:#fff;
}
*{box-sizing:border-box;margin:0;padding:0}
html,body{width:1200px;height:983px;overflow:hidden;background:var(--white)}
body{font-family:"Open Sans",Arial,sans-serif;color:var(--ink);position:relative}
.abs{position:absolute}
.top-rule{left:0;top:0;width:1200px;height:4px;background:var(--login-bg)}

/* login */
.login{left:827px;top:0;width:373px;height:51px;background:var(--login-bg);border-bottom-left-radius:8px}
.login .field{position:absolute;top:12px;height:24px;background:var(--field);border:1px solid #aaa;font-size:13px;font-style:italic;color:#666;padding:3px 14px}
.login .user{left:29px;width:115px}
.login .pass{left:156px;width:113px}
.login .btn{position:absolute;left:281px;top:12px;width:69px;height:24px;border-radius:12px;background:linear-gradient(#e6e6e6,#9a9a9a);font-size:12px;text-align:center;line-height:24px;color:#222}

/* brand */
.brand{left:34px;top:40px;display:flex;align-items:center;gap:14px}
.brand-mark{width:56px;height:56px;background:var(--accent)}
.brand-name{font-size:40px;font-weight:700;color:var(--ink);line-height:1}
.brand-tag{left:128px;top:84px;font-size:13px;letter-spacing:1.5px;color:#444;font-weight:600}

/* location */
.location{left:845px;top:68px;width:355px;height:56px;background:var(--panel);border-top-left-radius:10px}
.location .label{position:absolute;left:20px;top:18px;font-size:16px;color:#444}
.location .select{position:absolute;left:99px;top:16px;width:228px;height:29px;background:var(--white);border:1px solid #bbb;border-radius:3px;font-size:14px;padding:5px 22px}
.location .select::after{content:"⬍";position:absolute;right:0;top:0;width:22px;height:27px;border-left:1px solid #ccc;font-size:12px;text-align:center;line-height:27px;color:#555}

/* filter bar */
.filter-bar{left:0;top:124px;width:1200px;height:62px;background:var(--bar);color:var(--white)}
.filter-bar .search{position:absolute;left:34px;top:16px;width:157px;height:28px;background:var(--white);font-size:13px;font-style:italic;color:#333;padding:5px 12px}
.filter-bar .search svg{position:absolute;right:6px;top:5px}
.filter-bar .lbl{position:absolute;top:19px;font-size:14px}
.filter-bar .date{position:absolute;top:15px;width:86px;height:25px;background:var(--white)}
.filter-bar .cal{position:absolute;top:14px}
.days{position:absolute;left:702px;top:10px;width:220px;height:44px;font-size:11px}
.day{position:absolute;display:flex;align-items:center;gap:8px}
.day i{display:block;width:12px;height:12px;background:#555;border:1px solid #777}
.day i.on{background:#ddd}
.filter-bar .time{position:absolute;left:935px;top:18px;width:163px;height:25px;background:var(--white);color:#333;font-size:11px;padding:5px 14px}
.filter-bar .time span{position:absolute;right:2px;top:2px;width:20px;height:20px;border-radius:50%;background:#333;color:#fff;text-align:center;line-height:20px;font-size:10px}
.filter-bar .go{position:absolute;left:1110px;top:18px;width:70px;height:24px;border-radius:12px;background:linear-gradient(#c9c9c9,#7d7d7d);color:#fff;font-size:13px;text-align:center;line-height:24px}
.filter-bar .close{position:absolute;left:1180px;top:2px;width:17px;height:17px;background:var(--white);color:#000;font-size:12px;text-align:center;line-height:17px;border-radius:2px}

/* sidebar */
.side-head{position:absolute;left:14px;width:274px;height:37px;background:var(--black);color:var(--white);border-radius:8px 8px 0 0;font-size:15px;padding:8px 31px}
.side-body{position:absolute;left:14px;width:274px;background:var(--panel);border-radius:0 0 8px 8px}
.cats{list-style:none;position:absolute;left:38px;top:20px}
.cats li{height:36px;display:flex;align-items:center;gap:9px;font-size:15px}
.cats li b{display:inline-block;width:13px;height:13px;border-radius:50%;background:#333;color:#fff;font-size:11px;line-height:13px;text-align:center;font-weight:700}
.refine .k{position:absolute;left:22px;font-size:15px;font-weight:700}
.refine .k small{font-weight:400;font-size:12px;color:#555}
.slider{position:absolute;left:48px;width:182px;height:8px;border-radius:4px;background:linear-gradient(#999,#666)}
.slider i{position:absolute;top:-5px;width:17px;height:17px;border-radius:50%;background:radial-gradient(circle,var(--accent) 35%,#ddd 40%);border:1px solid #999}

/* listing */
.list-head{left:304px;top:204px;width:878px;height:36px;background:var(--black);color:var(--white);border-radius:10px;font-size:15px}
.list-head span{position:absolute;top:7px}
.card{position:absolute;left:304px;width:880px;background:var(--card);border:1px solid var(--card-line)}
.thumb{position:absolute;left:14px;top:14px;width:92px;height:90px;border:3px solid #ddd}
.title{position:absolute;left:125px;top:6px;font-size:15px;color:var(--accent)}
.desc{position:absolute;left:125px;top:28px;width:474px;font-size:12px;line-height:18px;text-align:justify;color:#222}
.sched{position:absolute;left:636px;top:4px;font-size:12px;line-height:18px;color:var(--muted)}
.venue{position:absolute;left:712px;top:25px;width:100px;text-align:center;font-size:12px}
.pin{position:absolute;left:733px;top:58px}
.price{position:absolute;left:792px;top:22px;width:100px;text-align:center;font-size:26px}
.price small{display:block;font-size:12px;line-height:18px;margin-top:3px}

/* footer */
.footer{left:0;top:856px;width:1200px;height:127px;background:var(--black);color:var(--white);font-size:15px;line-height:20px}
.footer .col{position:absolute;top:16px}
.footer h4{font-weight:400;color:var(--accent);font-size:15px}
</style>
</head>
<body>

<div class="abs top-rule"></div>

<div class="abs login">
  <div class="field user">User Name</div>
  <div class="field pass">Password</div>
  <div class="btn">Login</div>
</div>

<div class="abs brand">
  <div class="brand-mark"></div>
  <div class="brand-name">Out &amp; About</div>
</div>
<div class="abs brand-tag">GET OUT AND DISCOVER SOMETHING NEW</div>

<div class="abs location">
  <div class="label">Location</div>
  <div class="select">Prahran</div>
</div>

<div class="abs filter-bar">
  <div class="search">Search
    <svg width="18" height="18" viewBox="0 0 18 18"><circle cx="7" cy="7" r="5" fill="none" stroke="#333" stroke-width="2"/><line x1="11" y1="11" x2="16" y2="16" stroke="#333" stroke-width="2.5"/></svg>
  </div>
  <div class="lbl" style="left:304px">Date From</div>
  <div class="date" style="left:377px"></div>
  <svg class="cal" style="left:467px" width="29" height="28" viewBox="0 0 29 28"><rect x="1" y="2" width="27" height="25" rx="2" fill="#fff" stroke="#d22"/><rect x="1" y="2" width="27" height="7" fill="#d22"/><text x="17" y="23" font-size="8" fill="#222" font-family="Open Sans,sans-serif">21</text></svg>
  <div class="lbl" style="left:518px">To</div>
  <div class="date" style="left:542px"></div>
  <svg class="cal" style="left:634px" width="29" height="28" viewBox="0 0 29 28"><rect x="1" y="2" width="27" height="25" rx="2" fill="#fff" stroke="#d22"/><rect x="1" y="2" width="27" height="7" fill="#d22"/><text x="17" y="23" font-size="8" fill="#222" font-family="Open Sans,sans-serif">21</text></svg>
  <div class="days">
    <div class="day" style="left:0;top:0"><i class="on"></i>Mon</div>
    <div class="day" style="left:58px;top:0"><i></i>Tue</div>
    <div class="day" style="left:108px;top:0"><i></i>Wed</div>
    <div class="day" style="left:162px;top:0"><i></i>Thu</div>
    <div class="day" style="left:0;top:22px"><i></i>Fri</div>
    <div class="day" style="left:58px;top:22px"><i></i>Sat</div>
    <div class="day" style="left:108px;top:22px"><i></i>Sun</div>
    <div class="day" style="left:162px;top:22px"><i></i>All</div>
  </div>
  <div class="time">Any Time of Day<span>▾</span></div>
  <div class="go">Filter</div>
  <div class="close">✕</div>
</div>

<!-- sidebar -->
<div class="side-head" style="top:204px">Exlore Coursees &amp; Activities</div>
<div class="side-body" style="top:241px;height:353px">
  <ul class="cats">
    <li><b>+</b>Visual Arts (32)</li>
    <li><b>+</b>Cooking (14)</li>
    <li><b>+</b>Health / Fitnes (19)</li>
    <li><b>+</b>Home / Life (12)</li>
    <li><b>+</b>Languages (31)</li>
    <li><b>+</b>Performing Arts (28)</li>
    <li><b>+</b>Professional (5)</li>
    <li><b>+</b>Tech/ Internet (8)</li>
    <li><b>+</b>Arts and Sciences (9)</li>
  </ul>
</div>

<div class="side-head" style="top:618px;height:30px;padding:5px 25px;font-size:14px;background:#333">Refine Search ( recommented)</div>
<div class="side-body refine" style="top:648px;height:190px">
  <div class="k" style="top:14px">Age: <small>18 yrs+</small></div>
  <div class="slider" style="top:48px"><i style="left:52px"></i></div>
  <div class="k" style="top:92px">Max Price: <small>$50</small></div>
  <div class="slider" style="top:136px"><i style="left:42px"></i></div>
</div>

<!-- listing -->
<div class="abs list-head">
  <span style="left:14px">Showing: All Courses &amp; Activities</span>
  <span style="left:619px">Schedule</span>
  <span style="left:727px">Location</span>
  <span style="left:820px">Price</span>
</div>

<div class="card" style="top:258px;height:139px">
  <div class="thumb" role="img" aria-label="Photo of a couple dancing salsa" style="background:linear-gradient(135deg,#a85a22,#5a2d14)"></div>
  <div class="title">Salsa Patterns</div>
  <p class="desc">The standard chunk of Lorem Ipsum used since the 1500s is reproduced below for those interested. Sections 1.10.32 and 1.10.33 from "de Finibus Bonorum et Malorum" by Decimus are also reproduced in their exact original form, accompanied by English versions from the 1914 translation by J. Ellery</p>
  <div class="sched">M 6pm<br>T &nbsp;6px<br>W 5px, 7pm<br>T &nbsp;-<br>F &nbsp;- 7px<br>S &nbsp;-<br>S &nbsp;-</div>
  <div class="venue">South Bank</div>
  <svg class="pin" width="47" height="47" viewBox="0 0 47 47"><rect x="1" y="1" width="45" height="45" rx="9" fill="#ddd" stroke="#888"/><path d="M6 30 L40 14 M14 6 L30 42" stroke="#fff" stroke-width="4"/><line x1="28" y1="14" x2="28" y2="28" stroke="#555" stroke-width="1.5"/><circle cx="28" cy="14" r="3" fill="#d22"/></svg>
  <div class="price">$15<small>Single<br>Session</small></div>
</div>

<div class="card" style="top:407px;height:139px">
  <div class="thumb" role="img" aria-label="Photo of a tango pair mid-step" style="background:linear-gradient(135deg,#3a2030,#0e0e18)"></div>
  <div class="title">Argenine Tango - Intermediate</div>
  <p class="desc">The standard chunk of Lorem Ipsum used since the 1500s is reproduced below for those interested. Sections 1.10.32 and 1.10.33 from "de Finibus Bonorum et Malorum" by Decimus are also reproduced in their exact original form, accompanied by English versions from the 1914 translation by J. Ellery</p>
  <div class="sched">M 6pm<br>T &nbsp;6px<br>W 5px, 7pm<br>T &nbsp;-<br>F &nbsp;- 7px<br>S &nbsp;-<br>S &nbsp;-</div>
  <div class="venue">South Bank</div>
  <svg class="pin" width="47" height="47" viewBox="0 0 47 47"><rect x="1" y="1" width="45" height="45" rx="9" fill="#ddd" stroke="#888"/><path d="M6 30 L40 14 M14 6 L30 42" stroke="#fff" stroke-width="4"/><line x1="28" y1="14" x2="28" y2="28" stroke="#555" stroke-width="1.5"/><circle cx="28" cy="14" r="3" fill="#d22"/></svg>
  <div class="price">$60<small>Single<br>Session</small></div>
</div>

<div class="card" style="top:554px;height:140px">
  <div class="thumb" role="img" aria-label="Photo of a mat exercise class" style="background:linear-gradient(135deg,#c9b89a,#6d6a63)"></div>
  <div class="title">Kick Your Booty Mat</div>
  <p class="desc">The standard chunk of Lorem Ipsum used since the 1500s is reproduced below for those interested. Sections 1.10.32 and 1.10.33 from "de Finibus Bonorum et Malorum" by Decimus are also reproduced in their exact original form, accompanied by English versions from the 1914 translation by J. Ellery</p>
  <div class="sched">M 6pm<br>T &nbsp;6px<br>W 5px, 7pm<br>T &nbsp;-<br>F &nbsp;- 7px<br>S &nbsp;-<br>S &nbsp;-</div>
  <div class="venue">South Bank</div>
  <svg class="pin" width="47" height="47" viewBox="0 0 47 47"><rect x="1" y="1" width="45" height="45" rx="9" fill="#ddd" stroke="#888"/><path d="M6 30 L40 14 M14 6 L30 42" stroke="#fff" stroke-width="4"/><line x1="28" y1="14" x2="28" y2="28" stroke="#555" stroke-width="1.5"/><circle cx="28" cy="14" r="3" fill="#d22"/></svg>
  <div class="price">$54<small>Single<br>Session</small></div>
</div>

<div class="card" style="top:716px;height:124px">
  <div class="thumb" role="img" aria-label="Photo of a ballroom dancer on stage" style="background:linear-gradient(135deg,#1b1f4a,#6b6fa8)"></div>
  <div class="title">Ballroom Dancing for Beginers</div>
  <p class="desc">The standard chunk of Lorem Ipsum used since the 1500s is reproduced below for those interested. Sections 1.10.32 and 1.10.33 from "de Finibus Bonorum et Malorum" by Decimus are also reproduced in their exact original form, accompanied by English versions from the 1914 translation by J. Ellery</p>
  <div class="sched">M 6pm<br>T &nbsp;6px<br>W 5px, 7pm<br>T &nbsp;-<br>F &nbsp;- 7px<br>S &nbsp;-<br>S &nbsp;-</div>
  <div class="venue">South Bank</div>
  <svg class="pin" width="47" height="47" viewBox="0 0 47 47"><rect x="1" y="1" width="45" height="45" rx="9" fill="#ddd" stroke="#888"/><path d="M6 30 L40 14 M14 6 L30 42" stroke="#fff" stroke-width="4"/><line x1="28" y1="14" x2="28" y2="28" stroke="#555" stroke-width="1.5"/><circle cx="28" cy="14" r="3" fill="#d22"/></svg>
  <div class="price">$83<small>Single<br>Session</small></div>
</div>

<footer class="abs footer">
  <div class="col" style="left:312px"><h4>Contact Us</h4></div>
  <div class="col" style="left:485px"><h4>Customers</h4>Register<br>Login<br>Manage Booking</div>
  <div class="col" style="left:630px"><h4>Business</h4>&nbsp;Register<br>&nbsp;List a Class or Activity</div>
</footer>

</body>
</html>
```